Recruiting Firm Need Professional, Modern Tri-Fold Brochure for their United States Based Business

-We need a professional, modern TRI-FOLD brochure design that can help generate business for our recruiting firm. We need an impressive brochure.
- Please use the about us website content and attached website content. Website: www.morvellstaffingpartners.example
- Please use logo files attached.
- Please note: This brochure will be the starting point for an upgraded website design so we are NOT looking for a brochure to look like our current website.
- We want potential clients to want to do business with us just based on the brochure look and feel alone.

Target Market(s)

small, medium, and large companies who need administrative, human resources, and accounting talent

Industry/Entity Type

Professional Service

Font styles to use
Serif

Requirements
Must have
• - Professional, Modern TRI-FOLD Brochure Design for United States Based Company
• - Please show diverse group of professionals pictures similar to the ones on our website. One pic must include an African American female and one pic must include an African male. Or both an African American female and male can be include in the group of other races. But All the group photos must be diverse in race and include both male and female.
• - Please show pics of one business professional too
• a diverse group photo would be nice on the front cover...so we can show diversity and inclusion from the start
Should not have
• - Please DO NOT use the same pictures on our website.

```html
<!DOCTYPE html>
<html lang="en">
<head>
<meta charset="utf-8">
<title>Morvell Staffing Partners – Tri-Fold Brochure Inside</title>
<link href="https://fonts.googleapis.com/css2?family=Open+Sans:wght@300;400;600;700&display=swap" rel="stylesheet">
<style>
:root{
  --stage:#2b2b2b;
  --paper:#ffffff;
  --red:#b5080e;
  --red-dark:#7d0407;
  --ink:#2a2a2a;
  --black:#111111;
  --white:#ffffff;
}
*{box-sizing:border-box;margin:0;padding:0}
html,body{width:1200px;height:800px;overflow:hidden;background:var(--stage);font-family:"Open Sans",Arial,sans-serif}
.brochure{position:absolute;left:105px;top:20px;width:990px;height:760px;background:var(--paper);overflow:hidden;box-shadow:0 10px 30px rgba(0,0,0,.5)}
.panel{position:absolute;top:0;height:100%;width:330px}
.panel--about{left:0;background:var(--paper)}
.panel--difference{left:330px;background:linear-gradient(90deg,#f4f4f4,#ececec)}
.panel--cover{left:660px;background:linear-gradient(90deg,#ececec,#f2f2f2)}
.fold{position:absolute;top:0;width:1px;height:100%;background:rgba(0,0,0,.08);z-index:5}
.tab{position:absolute;top:38px;height:30px;background:var(--red);color:var(--white);font-weight:600;font-size:15px;line-height:30px;border-bottom:4px solid var(--black);white-space:nowrap}
.tab--left{left:0;width:220px;padding-left:28px;clip-path:polygon(0 0,92% 0,100% 100%,0 100%)}
.tab--right{right:0;width:310px;padding-left:36px;clip-path:polygon(0 0,100% 0,100% 100%,8% 100%)}
.subhead{position:absolute;color:var(--red);font-weight:700;font-size:13px;line-height:17px}
.about-sub{left:28px;top:86px;width:290px}
.about-copy{position:absolute;left:28px;top:132px;width:276px;font-size:11.5px;line-height:17px;color:var(--ink);text-align:justify}
.diff-sub{left:24px;top:86px;width:290px}
.checklist{position:absolute;left:24px;top:130px;width:290px;list-style:none}
.checklist li{position:relative;padding-left:20px;font-size:11px;line-height:15px;color:var(--ink);margin-bottom:12px}
.checklist svg{position:absolute;left:0;top:2px}
.headline{position:absolute;left:40px;top:38px;width:270px;color:var(--red);font-weight:400;font-size:30px;line-height:38px}
.photo{position:absolute}
.photo--professional{left:40px;top:400px;width:260px;height:210px;background:radial-gradient(ellipse at 60% 40%,#6b5a52 0%,#3a3a44 45%,#e8e8e8 80%)}
.photo--team{left:380px;top:320px;width:610px;height:300px;background:radial-gradient(ellipse at 55% 45%,#cfd8d8 0%,#b9c1c4 35%,#e9e4e0 70%,#f3f3f3 100%)}
.waves{position:absolute;left:0;bottom:0;width:990px;height:260px;z-index:4}
.contact{position:absolute;z-index:6;color:var(--white)}
.contact__phone{display:flex;align-items:center;gap:8px;font-size:19px;font-weight:400}
.contact__web{display:flex;align-items:center;gap:7px;font-size:12px;margin-top:4px;white-space:nowrap}
.contact--left{left:58px;top:680px}
.contact--right{left:720px;top:680px}
</style>
</head>
<body>
<main class="brochure">
  <section class="panel panel--about">
    <div class="tab tab--left">Who We Are</div>
    <h2 class="subhead about-sub">A Top-Notch Resource for Administrative, Human Resources, and Accounting Talent</h2>
    <p class="about-copy">Morvell Staffing Partners is a professional search firm that specializes in providing top-notch administrative, human resources, and accounting talent. We provide best-in-class talent to companies seeking to simplify their recruiting process, increase efficiency, and optimize productivity. Each search is customized based on our client's unique requirements. We provide quality, timely, and efficient services. Our recruiters are highly skilled in identifying, screening, interviewing, and assessing candidates across various industries. We develop a partnership with our client and candidate in order to make the recruitment process a success for both parties.</p>
    <div class="photo photo--professional" role="img" aria-label="Photo of a smiling business professional seated at a desk"></div>
  </section>

  <section class="panel panel--difference">
    <div class="tab tab--right">Experience the Morvell Difference</div>
    <h2 class="subhead diff-sub">We use our proprietary M-Strategy approach to deliver high-quality results.</h2>
    <ul class="checklist">
      <li><svg width="12" height="10" viewBox="0 0 12 10"><path d="M1 5l3.5 3.5L11 1" fill="none" stroke="#b5080e" stroke-width="2"/></svg>Top-Notch Talent. We will only present candidates who meet 90% of your job requirements.</li>
      <li><svg width="12" height="10" viewBox="0 0 12 10"><path d="M1 5l3.5 3.5L11 1" fill="none" stroke="#b5080e" stroke-width="2"/></svg>Thorough. We listen to your needs and develop a recruiting checklist to make sure we cover all basis.</li>
      <li><svg width="12" height="10" viewBox="0 0 12 10"><path d="M1 5l3.5 3.5L11 1" fill="none" stroke="#b5080e" stroke-width="2"/></svg>Tenacious. We are passionate and persistent about meeting your expectations.</li>
      <li><svg width="12" height="10" viewBox="0 0 12 10"><path d="M1 5l3.5 3.5L11 1" fill="none" stroke="#b5080e" stroke-width="2"/></svg>Timely. We deliver quality results on time.</li>
    </ul>
  </section>

  <section class="panel panel--cover">
    <h1 class="headline">We can find the right talent for your hiring needs.</h1>
  </section>

  <div class="photo photo--team" role="img" aria-label="Photo of a diverse team of professionals meeting around a glass conference table"></div>

  <svg class="waves" viewBox="0 0 990 260" preserveAspectRatio="none" aria-hidden="true">
    <path d="M0,18 C300,8 500,58 660,68 C800,58 900,8 990,-32 L990,260 L0,260Z" fill="#111111"/>
    <path d="M0,34 C300,24 500,74 660,84 C800,74 900,24 990,-16 L990,260 L0,260Z" fill="#7d0407"/>
    <path d="M0,56 C300,46 500,96 660,106 C800,96 900,46 990,6 L990,260 L0,260Z" fill="#ffffff"/>
    <path d="M0,72 C300,62 500,112 660,122 C800,112 900,62 990,22 L990,260 L0,260Z" fill="#b5080e"/>
  </svg>
  <div class="fold" style="left:330px"></div>
  <div class="fold" style="left:660px"></div>

  <div class="contact contact--left">
    <div class="contact__phone"><svg width="16" height="16" viewBox="0 0 16 16"><circle cx="8" cy="8" r="7" fill="none" stroke="#fff" stroke-width="1.3"/><path d="M5.5 4.5l1.5 1.5-1 1c.6 1.2 1.3 1.9 2.5 2.5l1-1 1.5 1.5-1 1c-2.5-.4-4.6-2.5-5-5z" fill="#fff"/></svg>555-014-2290</div>
    <div class="contact__web"><svg width="11" height="11" viewBox="0 0 12 12"><circle cx="6" cy="6" r="5" fill="none" stroke="#fff"/><path d="M1 6h10M6 1c-2 2.5-2 7.5 0 10M6 1c2 2.5 2 7.5 0 10" fill="none" stroke="#fff" stroke-width=".8"/></svg>www.morvellstaffingpartners.example</div>
  </div>
  <div class="contact contact--right">
    <div class="contact__phone"><svg width="16" height="16" viewBox="0 0 16 16"><circle cx="8" cy="8" r="7" fill="none" stroke="#fff" stroke-width="1.3"/><path d="M5.5 4.5l1.5 1.5-1 1c.6 1.2 1.3 1.9 2.5 2.5l1-1 1.5 1.5-1 1c-2.5-.4-4.6-2.5-5-5z" fill="#fff"/></svg>555-014-2290</div>
    <div class="contact__web"><svg width="11" height="11" viewBox="0 0 12 12"><circle cx="6" cy="6" r="5" fill="none" stroke="#fff"/><path d="M1 6h10M6 1c-2 2.5-2 7.5 0 10M6 1c2 2.5 2 7.5 0 10" fill="none" stroke="#fff" stroke-width=".8"/></svg>www.morvellstaffingpartners.example</div>
  </div>
</main>
</body>
</html>
```